Financial Broker firm looking for Brochure design/Pdf-document

Job Type
Brochure Design/PDF-Document
Task Outline
Create a Brochure Design that also works for sending as pdf-document.
Task Description
We need a combined corporate brochure (Booklet style) to give out to potential clients as well as sending it to potential clients through Internet as pdf-document.
We need a background template with pictures and colors that gives the impression of professionalism, trustworthiness and seriousness. Attached text in English but the text will be translated into different languages to fit different markets. Therefore we would like to receive one template including the text and one without any text (but with the logo). Please inform us where (any) pictures and/or photos on the template have been taken from in order for us to buy and use them legally.
About Us
Our company Quelvo Brokerage AB is a financial brokerage company who provides a diversity of services for different selected partners (www.quelvobrokerage.example).
Target Market
Companies on all levels, domestic or international
Requirements
Must Have:
-The text and logo attached below
Industry/Entity Type
Financial
Look and feel
Each slider illustrates characteristics of the customer's brand and the style your logo design should communicate.

```html
<!DOCTYPE html>
<html lang="en">
<head>
<meta charset="utf-8">
<title>Quelvo Brokerage – Brochure Cover</title>
<link rel="stylesheet" href="https://fonts.googleapis.com/css2?family=Alfa+Slab+One&family=Inter:wght@300;400;700&display=swap">
<style>
  :root {
    --stage: #050606;
    --sky: #00ccff;
    --sky-shade: #1cb8f2;
    --paper: #ffffff;
    --ink: #0b0b0b;
    --fold: #111111;
  }
  html, body {
    margin: 0;
    width: 1200px;
    height: 1000px;
    overflow: hidden;
    background: var(--stage);
  }
  .spread {
    position: relative;
    width: 1200px;
    height: 1000px;
  }
  .page {
    position: absolute;
    top: 152px;
    height: 696px;
    overflow: hidden;
    background: var(--sky);
  }
  .page--back { left: 134px; width: 465px; }
  .page--front { left: 601px; width: 464px; }
  .fold-line {
    position: absolute;
    left: 599px; top: 152px;
    width: 2px; height: 696px;
    background: var(--fold);
  }

  /* Back page contact block */
  .contact {
    position: absolute;
    left: 48px;
    font-family: "Inter", Helvetica, Arial, sans-serif;
    color: var(--paper);
    font-size: 13.5px;
    line-height: 19.8px;
  }
  .contact--address { top: 448px; font-weight: 300; }
  .contact--person { top: 593px; font-weight: 400; }
  .contact p { margin: 0; }
  .contact-rule {
    position: absolute;
    left: 48px; top: 573px;
    width: 286px; height: 1px;
    background: rgba(255,255,255,0.75);
  }

  /* Front page */
  .masthead {
    position: absolute;
    left: 0; top: 0;
    width: 464px; height: 244px;
    background: var(--paper);
  }
  .masthead-notch {
    position: absolute;
    left: 333px; top: 243px;
  }
  .brand-name {
    position: absolute;
    right: 55px; top: 176px;
    margin: 0;
    font-family: "Inter", Helvetica, Arial, sans-serif;
    font-weight: 700;
    font-size: 29px;
    letter-spacing: 0.5px;
    color: var(--ink);
    line-height: 1;
    white-space: nowrap;
  }
  .tagline {
    position: absolute;
    left: 42px;
    margin: 0;
    font-family: "Alfa Slab One", "Rockwell", Georgia, serif;
    font-weight: 400;
    white-space: nowrap;
  }
  .tagline span { display: block; }
  .tagline--echo {
    top: 298px;
    color: var(--sky-shade);
    font-size: 84px;
    line-height: 100px;
  }
  .tagline--echo .big { font-size: 118px; line-height: 120px; }
  .tagline--main {
    top: 442px;
    color: var(--paper);
    font-size: 38px;
    line-height: 45px;
  }
  .tagline--main .big { font-size: 64px; line-height: 66px; }
  .footer-band {
    position: absolute;
    left: 0; top: 628px;
    width: 464px; height: 20px;
    background: var(--paper);
  }
</style>
</head>
<body>
<div class="spread">
  <section class="page page--back">
    <div class="contact contact--address">
      <p>Contact Adress:</p>
      <p>Quelvo Brokerage AB</p>
      <p>Lindtorget 14</p>
      <p>211 40 Malmö</p>
      <p>Sweden</p>
      <p>www.quelvobrokerage.example</p>
    </div>
    <div class="contact-rule"></div>
    <div class="contact contact--person">
      <p>Contacted by:</p>
      <p>Mattias Lerveaux-Dahl</p>
      <p>Tel: +46700123456</p>
    </div>
  </section>

  <div class="fold-line"></div>

  <section class="page page--front">
    <h2 class="tagline tagline--echo" aria-hidden="true">
      <span>A partner</span>
      <span>in need as</span>
      <span class="big">success</span>
    </h2>
    <div class="masthead">
      <p class="brand-name">QUELVO BROKERAGE</p>
    </div>
    <svg class="masthead-notch" width="52" height="30" viewBox="0 0 52 30" aria-hidden="true">
      <polygon points="0,0 52,0 26,28" fill="#ffffff"/>
    </svg>
    <h1 class="tagline tagline--main">
      <span>A partner</span>
      <span>in need as in</span>
      <span class="big">success</span>
    </h1>
    <div class="footer-band"></div>
  </section>
</div>
</body>
</html>
```